Tech Startup needs Cool Business Card Designs

Looking for help Polishing our Business Card designs. We are a startup in the Knowledge management space that is releasing a product called TideNook which is a personal and group Digital Library. We're looking for help making our card designs standout. We already have a bunch of files to work from. Just need someone with an experienced eye to put everything together.

Target Market(s)

Knowledge Workers: people who work with alot of digital information on a daily basis and have problems keeping track and organizing everything. Special business cases; Researchers, Teacher/Trainers, Project Managers, Group Organizers, Nonprofit community managers, business owners, etc

Industry/Entity Type

Business

Contact Information for Business Card

Two Sided;
1) Backside is a digital library. I included several examples in the attached files. The digital library MUST use all of the ICONS attached. The digital library must look modern and sleek building off the concepts on the two attached files "BACK_'
2) Front- just needs to use the color scheme and style of the back into a modern hip yet professional design

Requirements
Must have
• - Designs for two sides
• - Back must be a representation of a digital library using ALL of the ICONS provided
• - Front must include all the main fields from Front business card design (but no QR code)
• - Must use TideNook Logo on both Front & Back
Should not have
• Do NOT NEED AREA FOR QR CODE

```html
<!DOCTYPE html>
<html lang="en">
<head>
<meta charset="utf-8">
<title>TideNook Business Card – Front and Back</title>
<link rel="stylesheet" href="https://fonts.googleapis.com/css2?family=Josefin+Sans:wght@400;600;700&display=swap">
<style>
  :root {
    --bg: #e4e4e2;
    --card: #f4f4f4;
    --ink: #3a3a3a;
    --orange: #f05a2b;
    --blue: #2b73b3;
    --rule: #9a9a9a;
    --library-light: #dfe9f3;
    --library-mid: #c9d9ea;
  }
  * { margin: 0; padding: 0; box-sizing: border-box; }
  html, body { width: 1200px; height: 900px; overflow: hidden; }
  body {
    background: var(--bg);
    font-family: "Josefin Sans", sans-serif;
    color: var(--ink);
    position: relative;
  }
  .business-card {
    position: absolute;
    left: 250px;
    width: 700px;
    height: 400px;
    background: linear-gradient(160deg, #ffffff 0%, var(--card) 60%, #e9e9e9 100%);
    border-radius: 40px;
    overflow: hidden;
    box-shadow: 0 6px 20px rgba(0,0,0,0.12);
  }
  .card-front { top: 40px; }
  .card-back { top: 460px; }

  .brand {
    position: absolute;
    display: flex;
    align-items: center;
    gap: 12px;
  }
  .card-front .brand { left: 200px; top: 62px; }
  .card-back .brand { left: 0; right: 0; top: 40px; justify-content: center; }
  .brand-dot {
    width: 22px;
    height: 22px;
    border-radius: 50%;
    background: var(--orange);
  }
  .brand-name {
    font-size: 52px;
    font-weight: 700;
    color: var(--blue);
    line-height: 1;
  }
  .card-back .brand-name { font-size: 40px; }
  .card-back .brand-dot { width: 18px; height: 18px; }

  .holder {
    position: absolute;
    right: 365px;
    top: 168px;
    text-align: right;
    font-variant: small-caps;
    letter-spacing: 2px;
    line-height: 1.2;
  }
  .holder-name { font-size: 20px; font-weight: 700; }
  .holder-role { font-size: 15px; margin-top: 2px; }
  .holder-address { font-size: 15px; margin-top: 16px; line-height: 1.35; }
  .divider {
    position: absolute;
    left: 350px;
    top: 164px;
    width: 1px;
    height: 108px;
    background: var(--rule);
  }
  .contacts {
    position: absolute;
    left: 364px;
    top: 168px;
    list-style: none;
    font-size: 15px;
    letter-spacing: 2px;
    font-variant: small-caps;
  }
  .contacts li { display: flex; align-items: center; gap: 8px; height: 19px; }
  .contacts li.gap { margin-top: 10px; }
  .contact-icon { width: 14px; height: 14px; flex: none; }
  .waves { position: absolute; left: 0; bottom: 0; width: 700px; height: 190px; }

  .library-shelf {
    position: absolute;
    left: 60px;
    right: 60px;
    top: 120px;
    bottom: 50px;
    border-radius: 14px;
    background: linear-gradient(180deg, var(--library-light) 0%, var(--library-mid) 100%);
  }
  .back-band {
    position: absolute;
    left: 0;
    right: 0;
    bottom: 0;
    height: 22px;
    background: var(--blue);
    border-top: 6px solid var(--orange);
  }
</style>
</head>
<body>
  <section class="business-card card-front">
    <div class="brand">
      <span class="brand-dot"></span>
      <span class="brand-name">TideNook</span>
    </div>

    <div class="holder">
      <p class="holder-name">Mara Ellison</p>
      <p class="holder-role">Owner / C.E.O</p>
      <p class="holder-address">Suite # 410, Pier Bldg,<br>CA 94107</p>
    </div>

    <div class="divider"></div>

    <ul class="contacts">
      <li>
        <svg class="contact-icon" viewBox="0 0 20 20"><circle cx="10" cy="10" r="10" fill="#3a3a3a"/><path d="M6 5h3l1 3-2 1c1 2 2 3 3 3l1-2 3 1v3c-6 0-9-3-9-9z" fill="#fff"/></svg>
        415-208-3371
      </li>
      <li>
        <svg class="contact-icon" viewBox="0 0 20 20"><circle cx="10" cy="10" r="10" fill="#3a3a3a"/><rect x="7" y="4" width="6" height="12" rx="1" fill="#fff"/></svg>
        415-208-3372
      </li>
      <li>
        <svg class="contact-icon" viewBox="0 0 20 20"><circle cx="10" cy="10" r="10" fill="#3a3a3a"/><rect x="5" y="8" width="10" height="7" fill="#fff"/><rect x="7" y="4" width="6" height="4" fill="#fff"/></svg>
        415-208-3379
      </li>
      <li class="gap">
        <svg class="contact-icon" viewBox="0 0 20 20"><circle cx="10" cy="10" r="10" fill="#3a3a3a"/><rect x="5" y="6" width="10" height="8" fill="#fff"/><path d="M5 6l5 4 5-4" stroke="#3a3a3a" fill="none"/></svg>
        mara@tidenook.com
      </li>
      <li>
        <svg class="contact-icon" viewBox="0 0 20 20"><circle cx="10" cy="10" r="10" fill="#3a3a3a"/><circle cx="10" cy="10" r="6" fill="none" stroke="#fff" stroke-width="1.4"/><path d="M4 10h12M10 4c-3 3-3 9 0 12M10 4c3 3 3 9 0 12" stroke="#fff" stroke-width="1.2" fill="none"/></svg>
        www.tidenook.com
      </li>
    </ul>

    <svg class="waves" viewBox="0 0 700 190" preserveAspectRatio="none" aria-hidden="true">
      <path d="M0 20 C 90 90, 210 115, 365 125 C 490 133, 620 140, 700 168 L700 190 L0 190 Z" fill="var(--orange)"/>
      <path d="M0 64 C 110 124, 240 134, 380 138 C 505 142, 620 148, 700 176 L700 190 L0 190 Z" fill="#ffffff"/>
      <path d="M0 72 C 110 132, 240 142, 380 146 C 505 150, 620 156, 700 182 L700 190 L0 190 Z" fill="var(--blue)"/>
    </svg>
  </section>

  <section class="business-card card-back">
    <div class="brand">
      <span class="brand-dot"></span>
      <span class="brand-name">TideNook</span>
    </div>
    <div class="library-shelf" role="img" aria-label="Digital library illustration: shelves holding the product's document, media and folder icons"></div>
    <div class="back-band"></div>
  </section>
</body>
</html>
```